A5 Patient Information Booklet (Chiropractic Clinic) 4-8 pages

Here’s a polished, professional rewrite of your full brief and content, with clearer structure, corrected language, and a premium tone:

---

**Project Title:** Premium Patient Information Brochure (Chiropractic & Wellness Clinic)

---

### **Overview**

We are a health and wellness clinic seeking a premium, high-end patient information brochure to provide following a patient’s initial consultation and first treatment.

The purpose of this booklet is to:

* Reinforce trust and professionalism
* Help patients understand what to expect next
* Encourage adherence to care recommendations
* Position the clinic as calm, expert-led, and results-driven

---

### **Format**

* 4–8 page booklet (A5 or similar size)
* Print-ready and digital versions required

---

### **Target Audience**

Patients who have just completed their initial consultation and may have begun treatment. They may already be experiencing physical or mental changes, so the brochure should guide, reassure, and educate them on what comes next.

---

### **Tone & Style**

* Premium, calm, and reassuring
* Modern wellness aesthetic (not overly clinical)
* Clean layout with minimal clutter
* Soft, neutral colour palette (whites, creams, muted greens, soft blues)
* Elegant typography (e.g. Montserrat / Lato)
* High-end, trustworthy, and professional feel

---

### **Key Messages**

#### 1. Listen to Your Body

Patients may feel different after treatment. Reassure them that this is normal and part of the healing process.

#### 2. Post-Treatment Advice

* Stay well hydrated
* Rest if needed
* Avoid overexertion if the body requires recovery

#### 3. Healing is a Journey (Core Concept)

A strong visual metaphor of a **“road to recovery”** or **journey** should be central to the design.

This journey should clearly illustrate three phases:

* **Phase 1: Initial Care (Weeks 1–6)**
Focus: Reducing pain/discomfort, calming the body, and initiating response to treatment

* **Phase 2: Corrective Care (Weeks 6–12)**
Focus: Addressing underlying issues, improving function, and creating lasting change

* **Phase 3: Wellness / Maintenance (Ongoing)**
Focus: Maintaining progress, preventing relapse, and supporting long-term wellbeing

**Important:**

* Emphasise that this is not a quick fix
* Progress requires time and consistency
* Each patient follows an individualised care plan
* The journey should feel structured, positive, and achievable

#### 4. Personalised Care

Reinforce that every treatment plan is tailored specifically to the individual.

#### 5. Professional Reassurance

Patients should feel confident they are in expert hands and supported throughout their journey.

---

### **Design Direction**

* Use imagery that reflects calmness, progression, and wellness (e.g. pathways, nature, soft gradients)
* Avoid generic stock imagery
* **Only use original clinic images from website and social media**
* Prioritise white space and clarity
* Aim for a luxury spa/medical hybrid aesthetic

---

## **Content Structure (Page-by-Page)**

### **Front Cover**

* Clean, minimal, premium design
* Clinic branding

---

### **Page 1: Patient Case Summary**

**Title:** *Welcome to Fernwell Spine Studio*

Thank you for choosing Fernwell Spine Studio.

This booklet is designed to guide you through:

* What we found during your initial consultation
* Your personalised recommended treatment plan
* Your road to recovery
* Long-term wellness care
* Why we take the approach we do

---

### **Page 2: Your Care Journey**

**Stage 1: Your Initial Consultation**

Today we completed a comprehensive assessment of your health and function, including:

* Full case history and discussion of your symptoms and goals
* Orthopaedic and neurological testing
* Postural and movement assessment
* Initial treatment (where appropriate)

**What this tells us:**

* How your body is currently functioning
* Where areas of stress or dysfunction may be present
* The most appropriate and effective path forward for your care

---

### **Page 3: Your Suggested Treatment Plan**

Based on today’s findings, your recommended care plan is:

**______ treatments over ______ weeks**

This should be viewed alongside your *Road to Recovery* to help you understand what to expect.

We have also discussed:

* Expected timelines for improvement
* Available payment options

**After Treatment:**
It is common to feel different following treatment. This is a normal response as your body begins to adapt and respond.

We recommend:

* Staying well hydrated
* Allowing time for rest and recovery
* Avoiding overexertion if your body feels it needs it

---

### **Page 4: What to Expect Next**

Healing is not always linear—it is a process that occurs over time.

Your care will typically progress through the following stages:

* **Relief Care**
Focused on reducing discomfort and calming the body

* **Corrective Care**
Focused on addressing underlying issues and improving function
(This phase may include prescribed exercises)

* **Maintenance / Wellness Care**
Focused on sustaining progress, preventing recurrence, and supporting long-term health

---

### **Page 5: Understanding Chiropractic Care**

**What is Chiropractic?**
Chiropractic care focuses on the relationship between the spine, nervous system, and overall body function.

By improving spinal movement and alignment, chiropractic care helps support the nervous system, allowing the body to function and heal more effectively.

**About Fernwell Spine Studio**
At Fernwell Spine Studio, our approach is centred around personalised, patient-focused care. We aim to not only relieve symptoms but to address underlying causes and support long-term wellbeing.

---

### **Back Page**

* Clinic contact details
* Website
* Social media icons/handles

**Closing Message:**
“A healthier, stronger you—supported every step of the way.”

---

### **Deliverables**

* Print-ready PDF
* Editable source files

---

### **Additional Notes**

* The brochure should feel valuable and worth keeping
* Encourage long-term care in a subtle, non-pushy way
* Maintain clarity, readability, and strong visual hierarchy
* Balance professionalism with warmth and approachability

---

If you’d like, I can also turn this into **actual brochure copy (fully written, patient-facing text)** or help you refine it further for a designer.

Existing patients who want to feel better and look after themselves that is given after their initil consultation appointment

Chiropractic, wellness, health

• Montserrat or Lato

0094D4
00A9DD
6FCCEA
C7EBF8
E9F6FB
00AB8E
00BBA5
67D7C9
C6EFE9
E9F9F6
6B429C
8869AF
B7A5CE
E3DAEB
F3F0F8

• my own photos, look premium wellness, be clear and simple to understand for patients journey or what to expect next and over time
• USe my social media/website for ideas
• generic photos and images

```html
<!DOCTYPE html>
<html lang="en">
<head>
<meta charset="utf-8">
<title>Fernwell Spine Studio – Patient Information Booklet</title>
<link href="https://fonts.googleapis.com/css2?family=Libre+Baskerville:wght@400;700&family=Nunito:wght@400;600;700&display=swap" rel="stylesheet">
<style>
:root{
  --teal:#4aa9a8;
  --teal-deep:#3a9897;
  --pink:#f77dcc;
  --violet:#b08fe0;
  --blue:#72b2e2;
  --ink:#222;
  --white:#fff;
  --board:#333;
  --serif:"Libre Baskerville", Georgia, serif;
  --sans:"Nunito", Arial, sans-serif;
}
*{margin:0;padding:0;box-sizing:border-box}
html,body{width:998px;height:1200px;overflow:hidden;background:var(--board)}
.stage{position:absolute;left:0;top:0;width:1747px;height:2100px;transform:scale(.5713);transform-origin:0 0;background:var(--board);font-family:var(--sans);color:var(--ink)}
.spread{position:absolute;left:213px;width:1322px;background:var(--white);overflow:hidden}
.spread--outside{top:148px;height:882px}
.spread--inside{top:1071px;height:881px}
.abs{position:absolute}
ul{list-style:none}

/* ---------- outside spread ---------- */
.intro-bracket{left:0;top:0}
.intro-copy{left:72px;width:355px}
.section-title{font-family:var(--serif);font-weight:700;font-size:18px;letter-spacing:.6px;color:var(--teal);white-space:nowrap}
.short-rule{height:2px;width:50px;background:var(--teal)}
.intro-copy p{font-size:14.2px;line-height:21.6px}

.contact-blob{left:492px;top:82px;width:391px;height:505px;border-radius:0 70px 0 130px;background:linear-gradient(200deg,var(--pink) 0%,var(--violet) 55%,var(--blue) 100%)}
.contact-card{left:437px;top:0;width:394px;height:487px;background:var(--teal);border-radius:0 110px 0 95px;color:var(--white);text-align:center}
.brand-circle{left:129px;top:26px;width:134px;height:134px;border:4px solid var(--white);border-radius:50%}
.brand-name{left:0;width:394px;top:172px;font-family:var(--serif);font-size:23px;letter-spacing:.5px;white-space:nowrap}
.address{left:0;width:394px;top:244px;font-size:18px;line-height:24.5px;white-space:nowrap}
.contact-rule{left:15px;top:344px;width:345px;height:1px;background:rgba(255,255,255,.7)}
.website{left:0;width:380px;top:354px;font-size:22px;font-weight:700;white-space:nowrap}
.social{left:0;width:394px;top:422px;display:flex;justify-content:center;align-items:center;gap:8px;font-size:16px;font-weight:600}
.social-dot{width:22px;height:22px;border-radius:50%;background:var(--white)}

.photo-welcome{left:883px;top:0;width:439px;height:587px;background:linear-gradient(135deg,#e9e3dc,#c9ab8a 45%,#7a6a60)}
.welcome-blob{left:962px;top:442px;width:360px;height:440px;border-radius:0 0 0 130px;background:linear-gradient(200deg,var(--pink) 0%,var(--violet) 45%,var(--blue) 100%)}
.welcome-card{left:905px;top:327px;width:397px;height:492px;background:var(--teal);border-radius:0 95px 0 95px;color:var(--white)}
.welcome-card .centered{left:0;width:397px;text-align:center;white-space:nowrap}
.welcome-kicker{top:24px;font-family:var(--serif);font-size:28px}
.welcome-name{top:70px;font-family:var(--serif);font-weight:700;font-size:22px;letter-spacing:.3px}
.welcome-rule{left:150px;top:122px;width:84px;height:1px;background:rgba(255,255,255,.7)}
.welcome-thanks{top:140px;font-size:40px}
.welcome-sub{top:190px;font-size:20px}
.welcome-lead{top:228px;font-family:var(--serif);font-weight:700;font-size:18px;line-height:26px}
.welcome-list{left:24px;top:305px;font-size:15.5px;line-height:27.6px;white-space:nowrap}
.welcome-list li{display:flex;align-items:center;gap:6px}
.leaf{width:8px;height:14px;flex:none}

.photo-closing{left:0;top:588px;width:883px;height:294px;background:linear-gradient(100deg,#b49a82 0%,#e4ddd3 35%,#f4f1ec 60%,#9a8e80 100%)}
.closing-line{left:500px;top:662px;width:366px;text-align:center;font-family:var(--serif);font-weight:700;font-size:30px;line-height:42.6px;color:var(--white);letter-spacing:.6px;text-shadow:0 2px 6px rgba(0,0,0,.35);white-space:nowrap}

/* ---------- inside spread ---------- */
.photo-consult{left:0;top:0;width:889px;height:379px;background:linear-gradient(20deg,#8fb3e8 0%,#c99ad8 40%,#d677bb 75%,#ee9ad3 100%)}
.consult-title{left:20px;top:260px;width:400px;text-align:center;font-family:var(--serif);font-weight:700;font-size:34px;line-height:40px;color:var(--white);letter-spacing:.6px;white-space:nowrap}
.plan-heading{left:415px;top:20px;width:500px;text-align:center;font-family:var(--serif);font-weight:700;font-size:27px;line-height:39px;color:var(--white);text-shadow:0 2px 6px rgba(0,0,0,.3);letter-spacing:.5px;white-space:nowrap}
.plan-fill{left:492px;top:147px;width:340px;display:flex;align-items:center;gap:7px;color:var(--white);font-size:16px;white-space:nowrap}
.plan-fill .blank{height:1px;background:var(--white);flex:none}
.road-chart{left:524px;top:187px;width:273px;height:192px;border:6px solid #3d3d3d;background:linear-gradient(90deg,#fbe9ec 0%,#fff6dc 40%,#e6f6ee 75%,#e4f1fb 100%)}

.findings{left:0;top:379px;width:431px;height:502px;background:var(--white)}
.findings h3{font-weight:600;color:var(--ink)}
.assess-title{left:27px;top:26px;font-size:23px;line-height:31px;width:400px}
.findings .short-rule{left:24px}
.check-list{left:24px;font-size:14.5px;line-height:17px}
.check-list li{display:flex;gap:6px;margin-bottom:13.5px}
.check-list li svg{flex:none;margin-top:2px}

.care-panel{left:431px;top:379px;width:458px;height:502px;background:var(--teal);color:var(--white)}
.care-intro{left:0;width:472px;top:14px;text-align:center}
.care-intro .lead{font-size:14.5px}
.care-intro .road{font-size:22px;line-height:22px}
.care-intro .sub{font-size:13.5px}
.care-panel h3{left:36px;font-weight:400;font-size:24.5px}
.care-list{left:36px;font-size:15px;line-height:23px}
.care-list li{display:flex;align-items:center;gap:6px}
.care-note{left:36px;top:244px;width:400px;font-size:14.2px;line-height:17px}
.care-panel .short-rule{left:36px;background:rgba(255,255,255,.8)}
.advice-list{left:36px;top:341px;font-size:15px}
.advice-list li{display:flex;align-items:center;gap:8px;height:39px}
.advice-icon{width:36px;height:36px;border:1.5px solid var(--white);border-radius:50%;flex:none;display:flex;align-items:center;justify-content:center}

.stages{left:891px;top:0;width:431px;height:561px;background:var(--white);text-align:center}
.stages-title{left:0;width:440px;top:40px;font-family:var(--serif);font-weight:700;font-size:24px;line-height:31px;color:var(--teal);letter-spacing:.4px;white-space:nowrap}
.stages-lead{left:0;width:431px;top:158px;font-size:16px;font-weight:600;line-height:32px}
.stage-card{left:53px;width:322px;height:87px;background:var(--teal);border-radius:14px;color:var(--white);text-align:left}
.stage-card .icon{position:absolute;left:14px;top:13px;width:60px;height:60px;border:1.5px dashed rgba(255,255,255,.85);border-radius:50%;display:flex;align-items:center;justify-content:center}
.stage-card .name{position:absolute;left:86px;top:8px;font-size:16.5px;font-weight:700;white-space:nowrap}
.stage-card .name::after{content:"";display:block;width:24px;height:1px;background:var(--white);margin-top:4px}
.stage-card .desc{position:absolute;left:86px;top:39px;width:232px;font-size:12.8px;line-height:15px}
.stage-card .desc small{font-size:9px}
.photo-team{left:891px;top:561px;width:431px;height:320px;background:linear-gradient(120deg,#dcdcdc 0%,#8c8c8c 45%,#3e3e3e 100%)}
</style>
</head>
<body>
<div class="stage">

  <!-- Outside spread: about, contact, welcome -->
  <section class="spread spread--outside">
    <svg class="abs intro-bracket" width="437" height="480" viewBox="0 0 437 480" aria-hidden="true">
      <defs>
        <linearGradient id="bracketFade" x1="0" y1="0" x2="0" y2="1">
          <stop offset="0" stop-color="#f77dcc"/>
          <stop offset=".6" stop-color="#c48fdc"/>
          <stop offset="1" stop-color="#72b2e2"/>
        </linearGradient>
      </defs>
      <path d="M0 0H290Q365 5 380 72Q352 55 300 55H38V472Q14 448 0 420Z" fill="url(#bracketFade)"/>
    </svg>

    <div class="abs intro-copy" style="top:104px">
      <h2 class="section-title" style="font-size:19px">WHAT IS CHIROPRACTIC?</h2>
    </div>
    <div class="abs short-rule" style="left:78px;top:146px"></div>
    <div class="abs intro-copy" style="top:160px"><p>Chiropractic care focuses on the relationship between the spine, nervous system, and overall body function.</p></div>
    <div class="abs intro-copy" style="top:224px"><p>By improving spinal movement and alignment, chiropractic care helps support the nervous system, allowing the body to function and heal more effectively.</p></div>
    <div class="abs intro-copy" style="top:333px">
      <h2 class="section-title" style="font-size:16.5px">ABOUT FERNWELL SPINE STUDIO</h2>
    </div>
    <div class="abs short-rule" style="left:78px;top:367px"></div>
    <div class="abs intro-copy" style="top:376px"><p>At Fernwell Spine Studio, our approach is centred around personalised, patient-focused care. We aim to not only relieve symptoms but to address underlying causes and support long-term wellbeing.</p></div>

    <div class="abs contact-blob"></div>
    <div class="abs contact-card">
      <div class="abs brand-circle"></div>
      <div class="abs brand-name">FERNWELL SPINE STUDIO</div>
      <div class="abs address">Fernwell Spine Studio<br>Chiropractic &amp; Wellness<br>12 Marlow Lane, Avonbury AV5 3QT</div>
      <div class="abs contact-rule"></div>
      <div class="abs website">www.fernwellspinestudio.com</div>
      <div class="abs social"><span class="social-dot"></span>@fernwellspine</div>
    </div>

    <div class="abs photo-welcome" role="img" aria-label="Photo of the chiropractor smiling while treating a patient's upper back"></div>
    <div class="abs welcome-blob"></div>
    <div class="abs welcome-card">
      <div class="abs centered welcome-kicker">Welcome to</div>
      <div class="abs centered welcome-name">FERNWELL SPINE STUDIO</div>
      <div class="abs welcome-rule"></div>
      <div class="abs centered welcome-thanks">Thank you</div>
      <div class="abs centered welcome-sub">for choosing Fernwell Spine Studio.</div>
      <div class="abs centered welcome-lead">This booklet is designed to guide<br>you through</div>
      <ul class="abs welcome-list">
        <li><svg class="leaf" viewBox="0 0 8 14"><path d="M4 0C8 4 8 9 4 12C0 9 0 4 4 0ZM4 12V14" fill="#fff" stroke="#fff"/></svg>What we found during your initial consultation</li>
        <li><svg class="leaf" viewBox="0 0 8 14"><path d="M4 0C8 4 8 9 4 12C0 9 0 4 4 0ZM4 12V14" fill="#fff" stroke="#fff"/></svg>Your personalised recommended treatment plan</li>
        <li><svg class="leaf" viewBox="0 0 8 14"><path d="M4 0C8 4 8 9 4 12C0 9 0 4 4 0ZM4 12V14" fill="#fff" stroke="#fff"/></svg>Your road to recovery</li>
        <li><svg class="leaf" viewBox="0 0 8 14"><path d="M4 0C8 4 8 9 4 12C0 9 0 4 4 0ZM4 12V14" fill="#fff" stroke="#fff"/></svg>Long-term wellness care</li>
        <li><svg class="leaf" viewBox="0 0 8 14"><path d="M4 0C8 4 8 9 4 12C0 9 0 4 4 0ZM4 12V14" fill="#fff" stroke="#fff"/></svg>Why we take the approach we do</li>
      </ul>
    </div>

    <div class="abs photo-closing" role="img" aria-label="Photo of a patient lying face down while hands treat her back"></div>
    <div class="abs closing-line">A healthier,<br>stronger you<br>supported every<br>step of the way</div>
  </section>

  <!-- Inside spread: consultation, plan, stages -->
  <section class="spread spread--inside">
    <div class="abs photo-consult" role="img" aria-label="Photo of a patient receiving treatment, with a pink to blue colour wash"></div>
    <div class="abs consult-title">YOUR INITIAL<br>CONSULTATION</div>
    <div class="abs plan-heading">Based on today’s findings,<br>your recommended<br>care plan is</div>
    <div class="abs plan-fill">
      <span class="blank" style="width:82px"></span><span>treatments over</span><span class="blank" style="width:50px"></span><span>weeks</span>
    </div>
    <div class="abs road-chart" role="img" aria-label="Road to Recovery chart showing a winding path rising through relief, correction and maintenance phases over days, weeks, months and years"></div>

    <div class="abs findings">
      <h3 class="abs assess-title">Today we completed a comprehensive assessment of your health and function, including</h3>
      <div class="abs short-rule" style="top:135px"></div>
      <ul class="abs check-list" style="top:151px;width:330px">
        <li><svg width="14" height="14" viewBox="0 0 14 14"><path d="M7 1L13 7L7 13L1 7Z" fill="none" stroke="#e98ad0" stroke-width="1.5"/><path d="M7 4L10 7L7 10L4 7Z" fill="#e98ad0"/></svg><span>Full case history and discussion of your symptoms and goals</span></li>
        <li><svg width="14" height="14" viewBox="0 0 14 14"><path d="M7 1L13 7L7 13L1 7Z" fill="none" stroke="#e98ad0" stroke-width="1.5"/><path d="M7 4L10 7L7 10L4 7Z" fill="#e98ad0"/></svg><span>Orthopaedic and neurological testing</span></li>
        <li><svg width="14" height="14" viewBox="0 0 14 14"><path d="M7 1L13 7L7 13L1 7Z" fill="none" stroke="#e98ad0" stroke-width="1.5"/><path d="M7 4L10 7L7 10L4 7Z" fill="#e98ad0"/></svg><span>Postural and movement assessment</span></li>
        <li><svg width="14" height="14" viewBox="0 0 14 14"><path d="M7 1L13 7L7 13L1 7Z" fill="none" stroke="#e98ad0" stroke-width="1.5"/><path d="M7 4L10 7L7 10L4 7Z" fill="#e98ad0"/></svg><span>Initial treatment (where appropriate)</span></li>
      </ul>
      <h3 class="abs" style="left:24px;top:320px;font-size:22px">What this tells us</h3>
      <div class="abs short-rule" style="top:358px"></div>
      <ul class="abs check-list" style="top:373px;width:360px">
        <li><svg class="leaf" viewBox="0 0 8 14"><path d="M4 0C8 4 8 9 4 12C0 9 0 4 4 0ZM4 12V14" fill="#4aa9a8" stroke="#4aa9a8"/></svg><span>How your body is currently functioning</span></li>
        <li><svg class="leaf" viewBox="0 0 8 14"><path d="M4 0C8 4 8 9 4 12C0 9 0 4 4 0ZM4 12V14" fill="#4aa9a8" stroke="#4aa9a8"/></svg><span>Where areas of stress or dysfunction may be present</span></li>
        <li><svg class="leaf" viewBox="0 0 8 14"><path d="M4 0C8 4 8 9 4 12C0 9 0 4 4 0ZM4 12V14" fill="#4aa9a8" stroke="#4aa9a8"/></svg><span>The most appropriate and effective path forward for your care</span></li>
      </ul>
    </div>

    <div class="abs care-panel">
      <div class="abs care-intro">
        <div class="lead">This should be viewed alongside your</div>
        <div class="road">ROAD TO RECOVERY</div>
        <div class="sub">to help you understand what to expect.</div>
      </div>
      <h3 class="abs" style="top:83px">We have also discussed:</h3>
      <ul class="abs care-list" style="top:134px">
        <li><svg class="leaf" viewBox="0 0 8 14"><path d="M4 0C8 4 8 9 4 12C0 9 0 4 4 0ZM4 12V14" fill="#fff" stroke="#fff"/></svg>Expected timelines for improvement</li>
        <li><svg class="leaf" viewBox="0 0 8 14"><path d="M4 0C8 4 8 9 4 12C0 9 0 4 4 0ZM4 12V14" fill="#fff" stroke="#fff"/></svg>Available payment options</li>
      </ul>
      <h3 class="abs" style="top:198px">After Treatment</h3>
      <p class="abs care-note">It is common to feel different following treatment. This is a normal response as your body begins to adapt and respond</p>
      <h3 class="abs" style="top:300px;font-size:23.5px">We recommend:</h3>
      <div class="abs short-rule" style="top:336px"></div>
      <ul class="abs advice-list" style="top:349px">
        <li><span class="advice-icon"><svg width="18" height="18" viewBox="0 0 18 18"><path d="M9 2C12 7 14 9 14 12A5 5 0 0 1 4 12C4 9 6 7 9 2Z" fill="none" stroke="#fff" stroke-width="1.5"/></svg></span>Staying well hydrated</li>
        <li><span class="advice-icon"><svg width="18" height="18" viewBox="0 0 18 18"><path d="M2 13H16M3 13V8M3 10H15V13M6 9A1.5 1.5 0 1 0 6 6" fill="none" stroke="#fff" stroke-width="1.5"/></svg></span>Allowing time for rest and recovery</li>
        <li><span class="advice-icon"><svg width="18" height="18" viewBox="0 0 18 18"><circle cx="9" cy="4" r="2" fill="#fff"/><path d="M9 7V12M5 9H13M9 12L6 16M9 12L12 16" stroke="#fff" stroke-width="1.5" fill="none"/></svg></span>Avoiding overexertion if your body feels it needs it</li>
      </ul>
    </div>

    <div class="abs stages">
      <h2 class="abs stages-title">Healing is not always linear<br>it is a process that occurs<br>over time</h2>
      <p class="abs stages-lead">Your care will typically progress through the<br>following stages:</p>

      <div class="abs stage-card" style="top:243px">
        <span class="icon"><svg width="28" height="28" viewBox="0 0 28 28"><path d="M14 22C6 16 4 12 6 8C8 5 12 6 14 9C16 6 20 5 22 8C24 12 22 16 14 22Z" fill="none" stroke="#fff" stroke-width="1.5"/></svg></span>
        <span class="name">Relief Care</span>
        <span class="desc">Focused on reducing discomfort and calming the body</span>
      </div>
      <div class="abs stage-card" style="top:340px">
        <span class="icon"><svg width="28" height="28" viewBox="0 0 28 28"><path d="M14 22C6 16 4 12 6 8C8 5 12 6 14 9C16 6 20 5 22 8C24 12 22 16 14 22Z" fill="none" stroke="#fff" stroke-width="1.5"/><path d="M8 13H11L13 10L15 16L17 13H20" fill="none" stroke="#fff" stroke-width="1.3"/></svg></span>
        <span class="name">Corrective Care</span>
        <span class="desc">Focused on addressing underlying issues &amp; improving function <small>(This phase may include prescribed exercises)</small></span>
      </div>
      <div class="abs stage-card" style="top:440px">
        <span class="icon"><svg width="28" height="28" viewBox="0 0 28 28"><path d="M14 18C8 14 7 11 8.5 8.5C10 6.5 12.5 7 14 9C15.5 7 18 6.5 19.5 8.5C21 11 20 14 14 18Z" fill="#fff"/><path d="M4 20Q10 18 14 22Q18 20 24 20" fill="none" stroke="#fff" stroke-width="1.5"/></svg></span>
        <span class="name">Maintenance / Wellness Care</span>
        <span class="desc">Focused on sustaining progress, preventing recurrence, and supporting long-term health</span>
      </div>
    </div>

    <div class="abs photo-team" role="img" aria-label="Black and white photo of the chiropractor applying support tape to a smiling patient's shoulder"></div>
  </section>

</div>
</body>
</html>
```